Low Ferry Guild - Wavering CD Cover

To prepare a CD Cover for the single "Wavering" by Low Ferry Guild.
You can hear the single here:
http://lowferryguild-band.example/listen/

The LFG logo and backdrop are also provided if you want to incorporate them into the CD cover design, though that isn't mandatory.

Song is about deciding on taking on a serious relationship, and leaving the single life behind.

Target Market(s)

Music listeners, 18-50 yrs old, into retro 80s, Marrowmen/Tide Rollers

Industry/Entity Type

Music Download

Requirements
Must have
• LFG logo
• Wavering title
Nice to have
• Use of backdrop, or facimile
Should not have
• Too obvious on the term Wavering

```html
<!DOCTYPE html>
<html lang="en">
<head>
<meta charset="utf-8">
<title>Low Ferry Guild – Wavering</title>
<link rel="stylesheet" href="https://fonts.googleapis.com/css2?family=Big+Shoulders+Display:wght@400&family=Josefin+Sans:wght@300&display=swap">
<style>
  :root {
    --bg: #231f20;
    --band: #f2a7cb;
    --title: #ffffff;
  }
  html, body {
    margin: 0;
    padding: 0;
    width: 1200px;
    height: 1200px;
    overflow: hidden;
    background: var(--bg);
  }
  .cover {
    display: block;
    width: 1200px;
    height: 1200px;
  }
  .band-name {
    font-family: "Big Shoulders Display", sans-serif;
    font-weight: 400;
    fill: var(--band);
  }
  .single-title {
    font-family: "Josefin Sans", sans-serif;
    font-weight: 300;
    fill: var(--title);
  }
</style>
</head>
<body>
<svg class="cover" viewBox="0 0 1200 1200" xmlns="http://www.w3.org/2000/svg">
  <title>Low Ferry Guild – Wavering</title>

  <rect class="backdrop" width="1200" height="1200" fill="var(--bg)"/>

  <g class="band-name" role="img" aria-label="Low Ferry Guild">
    <text x="356" y="432" font-size="335" textLength="500" lengthAdjust="spacingAndGlyphs">LOW</text>
    <text x="356" y="724" font-size="305" textLength="500" lengthAdjust="spacingAndGlyphs">FERRY</text>
    <text x="356" y="934" font-size="203" textLength="500" lengthAdjust="spacingAndGlyphs">GUILD</text>
  </g>

  <text class="single-title" x="152" y="1080" font-size="52" textLength="930" lengthAdjust="spacing">WAVERING</text>
</svg>
</body>
</html>
```